Business Cards for IT Consulting Company (Managed Service Provider)

I am looking to have some business cards printed and would like some designs. We are an IT Consulting company based in Vancouver BC. I would like a nice clean and modern look to the cards. I have uploaded all the versions of my logo so parts can be used as needed. Here is a snippit from our website homepage:

Quillbrook Networks Ltd. is an IT Solutions Partner located in Vancouver BC, Canada. We offer IT solutions and support to customers in the greater Vancouver Area. With expertise in Microsoft platforms, as well as Linux and Mac OSX and over 12 years experience in the IT industry, Quillbrook Networks is dedicated to offering our clients top quality service and products. We take pride in the solutions we offer our customers. The greatest compliment a client can give us is to recommend our services.

Quillbrook Networks Ltd. offers a wide range of IT services from onsite service to remote support and managed service solutions. This allows clients to choose the support path that best suits their company’s needs. Supporting many different sized companies from small to enterprise level over the past 12 years Quillbrook Networks has the experience and expertise needed to ensure things run smoothly. Allowing our clients to focus on doing business.

Revolutionizing the way IT services are delivered.

Quillbrook Networks is dedicated to providing our clients with IT solutions that work and grow with them for years to come. This philosophy helps save money in the long run instead of replacing equipment constantly. Far too often IT solutions are not well thought out and while possibly solving the problem at hand, require replacement due to growth or quality within a very short time frame. Quillbrook Networks takes pride in providing solutions that will last and be able to accommodate growth without the need for replacement.

Industry/Entity Type

Information Technology

Contact Information for Business Card

Quillbrook Networks Ltd.
(Employee Name)
Eml: (Employees Email Address)
Web: quillbrook.me
Ph: 604-555-0148

Font styles to use
Serif
Sans Serif

Requirements
Must have
• The Company logo and company colors.
Nice to have
• - Our tag line: "Revolutionizing IT Services" or "Revolutionizing the way IT services are delivered."
• - Also I really like the idea of nature and technology together blending which is sort of where my logo came from so integrating that somehow onto the business cards would be great.

```html
<!DOCTYPE html>
<html lang="en">
<head>
<meta charset="utf-8">
<title>Quillbrook Networks Ltd. – Business Card</title>
<link rel="stylesheet" href="https://fonts.googleapis.com/css2?family=Montserrat:wght@600&family=Open+Sans:wght@400;600&display=swap">
<style>
  :root {
    --brand-blue: #1aa9e6;
    --brand-grey: #5b5d60;
    --text-grey: #555759;
    --card-white: #ffffff;
    --page-bg: #e9ecef;
  }
  * { margin: 0; padding: 0; box-sizing: border-box; }
  html, body {
    width: 1200px;
    height: 900px;
    overflow: hidden;
    background: var(--page-bg);
  }
  .business-card {
    position: absolute;
    left: 145px;
    top: 170px;
    width: 910px;
    height: 560px;
    background: var(--card-white);
    border-radius: 22px;
    overflow: hidden;
    box-shadow: 0 6px 24px rgba(0, 0, 0, 0.12);
    font-family: "Open Sans", Arial, sans-serif;
  }
  .card-band-top {
    position: absolute;
    left: 0; right: 0; top: 0;
    height: 24px;
    background: var(--brand-blue);
  }
  .card-band-bottom {
    position: absolute;
    left: 0; right: 0; bottom: 0;
    height: 22px;
    background: var(--brand-grey);
  }
  .holder-name {
    position: absolute;
    top: 62px;
    width: 100%;
    text-align: center;
    font-size: 31px;
    font-weight: 600;
    color: var(--text-grey);
  }
  .holder-name .first-name { color: var(--brand-blue); }
  .company-mark {
    position: absolute;
    top: 200px;
    width: 100%;
    display: flex;
    align-items: center;
    justify-content: center;
    gap: 22px;
  }
  .company-mark-square {
    width: 44px;
    height: 44px;
    background: var(--brand-blue);
  }
  .company-name {
    font-family: "Montserrat", Arial, sans-serif;
    font-weight: 600;
    font-size: 52px;
    color: var(--brand-blue);
    letter-spacing: 0.5px;
  }
  .contact-list {
    position: absolute;
    top: 398px;
    left: 0;
    width: 100%;
    display: grid;
    grid-template-columns: auto auto;
    justify-content: center;
    column-gap: 8px;
    row-gap: 8px;
    font-size: 24px;
    line-height: 30px;
    color: var(--text-grey);
  }
  .contact-label {
    text-align: right;
    font-weight: 600;
    color: var(--brand-blue);
  }
</style>
</head>
<body>
  <article class="business-card">
    <div class="card-band-top"></div>

    <h1 class="holder-name"><span class="first-name">Daniel</span> Hartley</h1>

    <div class="company-mark">
      <span class="company-mark-square"></span>
      <span class="company-name">Quillbrook Networks Ltd.</span>
    </div>

    <div class="contact-list">
      <span class="contact-label">T:</span><span class="contact-value">604-555-0148</span>
      <span class="contact-label">E:</span><span class="contact-value">info@quillbrook.me</span>
      <span class="contact-label">W:</span><span class="contact-value">www.quillbrook.me</span>
    </div>

    <div class="card-band-bottom"></div>
  </article>
</body>
</html>
```